Website Design Project for Beauty & Wellness Professionals

As background information, I have a website that is focused on Beauty & Wellness Professionals:
- Job Search (www.lumarinovo.com)
- Business Classifieds (negocios.lumarinovo.com)
- Freelancer Classifieds (freelancer.lumarinovo.com)
- Course Reviews (cursos.lumarinovo.com)

All those websites use standard templates.

I need a DESIGN for the HOME PAGE (no coding) of the Website Platform that consolidates the four platforms under the same design.

Website designs that we like:
- quelvox.com
- brintmoor.com

Target Market(s)

Brazilian Professionals from Beauty & Wellness sector

Industry/Entity Type

Business

Requirements
Must have
• Website designs that we like:
- quelvox.com
- brintmoor.com

```html
<!DOCTYPE html>
<html lang="pt-BR">
<head>
<meta charset="utf-8">
<title>Lumari Novo — Home</title>
<link href="https://fonts.googleapis.com/css2?family=Ubuntu:wght@400;500;700&display=swap" rel="stylesheet">
<style>
:root{
  --green:#8cc47a;
  --green-dark:#5ea33c;
  --orange:#e8764a;
  --orange-text:#d35f28;
  --teal:#5a9fb8;
  --sky:#9bd3e6;
  --sky-deep:#5bb4d8;
  --line:#dcdcdc;
  --panel:#f5f5f5;
  --text:#555;
  --dark:#333;
  --red:#d9412f;
}
*{box-sizing:border-box;margin:0;padding:0}
html,body{width:676px;height:1200px;overflow:hidden}
body{position:relative;background:#fff;font-family:'Ubuntu',sans-serif;color:var(--text);font-size:7px}
.abs{position:absolute}
.topbar{left:0;top:0;width:676px;height:22px;background:var(--green);color:#fff;font-size:6.5px;text-align:right;padding:8px 73px 0 0;letter-spacing:.2px}
.logo{left:74px;top:64px;display:flex;align-items:center;gap:6px;color:var(--teal);font-size:16px}
.logo .mark{width:16px;height:16px;border-radius:50%;background:var(--teal)}
.promo{left:194px;top:28px;width:409px;height:28px;background:linear-gradient(90deg,#7ec9e6,#a6dcef 60%,#f0e8e0);display:flex;align-items:center;justify-content:space-between;padding:0 6px 0 48px;font-weight:700}
.promo .left{color:#2e5a86;font-size:9.5px;line-height:10px;text-align:center}
.promo .right{color:#d4282a;font-size:9px;line-height:10px;text-align:right}
.nav{left:209px;top:65px;width:394px;height:25px;background:var(--orange);border-radius:3px;display:flex;justify-content:space-around;align-items:center;color:#fff;font-size:7.2px}
.hero{left:0;top:98px;width:676px;height:287px;background:linear-gradient(100deg,#6b4a36 0%,#b58b5f 30%,#d9b47a 55%,#e7cf9d 70%,#caa070 100%)}
.search{left:73px;top:234px;width:271px;height:66px;background:rgba(0,0,0,.78);border-radius:3px;padding:5px 8px;color:#fff}
.search h2{font-size:12px;font-weight:500;margin-bottom:5px}
.search .row{display:flex;gap:6px}
.search .field{width:195px;height:20px;background:#fff;border-radius:2px;color:#999;font-size:7px;font-style:italic;padding:6px 7px}
.search .btn{width:53px;height:20px;background:var(--green);border-radius:2px;text-align:center;font-size:9px;font-weight:500;padding-top:5px}
.search .ex{font-size:6px;margin-top:5px}
.dots{left:553px;top:364px;display:flex;gap:3px}
.dots i{width:10px;height:10px;border-radius:50%;background:#c9412a;display:block}
.subscribe{left:73px;top:394px;width:530px;height:52px;border:1px solid var(--line);border-radius:3px;background:#fafafa}
.subscribe .title{left:0;top:6px;color:var(--orange-text);font-size:9.5px;font-weight:500;text-align:right;width:131px;white-space:nowrap}
.subscribe .desc{left:7px;top:19px;width:124px;text-align:right;font-size:6px;line-height:9px}
.subscribe .email{left:137px;top:7px;width:142px;height:16px;border:1px solid var(--line);background:#fff;font-style:italic;color:#aaa;font-size:6px;padding:4px 7px}
.subscribe .sbtn{left:227px;top:29px;width:52px;height:15px;background:var(--sky-deep);border-radius:2px;color:#123;font-size:6.5px;font-weight:500;text-align:center;padding-top:4px}
.subscribe .follow{left:304px;top:17px;color:var(--orange-text);font-size:9.5px;font-weight:500}
.social{left:377px;top:11px;display:flex;gap:13px}
.social i{display:block;width:27px;height:27px;border-radius:50%}
.panel{border:1px solid var(--line);border-radius:3px;background:var(--panel)}
.tabs{left:83px;top:468px;display:flex;gap:2px}
.tab{height:23px;padding:6px 17px;font-size:7.8px;font-weight:500;border:1px solid var(--line);border-bottom:none;background:#eaeaea;color:var(--dark)}
.tab.on{background:#fff;color:var(--orange-text)}
.jobs{left:83px;top:490px;width:330px;height:322px;background:#fff;border:1px solid var(--line)}
.job{position:absolute;left:8px;width:312px;height:89px;border:1px solid var(--line);background:#fff}
.job .head{height:16px;background:#e8e8e8;display:flex;font-size:6.5px;color:var(--dark);font-weight:500}
.job .head span,.job .body>div{padding:4px 5px}
.c1{width:51px}.c2{width:134px}.c3{width:92px}.c4{width:35px}
.job .body{display:flex;height:50px;border-bottom:1px solid var(--line)}
.job .body>div{border-right:1px solid var(--line);font-size:6.3px;line-height:9.5px}
.job .body>div:last-child{border-right:none}
.thumb{width:27px;height:27px;border:1px solid var(--line);margin:2px 5px;background:linear-gradient(135deg,#f0d8c4,#c7a083)}
.g{color:var(--green-dark);font-weight:500;font-size:6.8px}
.small{font-size:5.6px;line-height:9px;color:#666}
.job .foot{display:flex;justify-content:space-between;align-items:center;height:22px;padding:0 6px;background:#fafafa;font-size:5.8px;font-style:italic}
.job .foot em{color:var(--orange-text)}
.badge{width:54px;height:15px;border-radius:2px;color:#fff;font-size:6px;text-align:center;line-height:6.5px;padding-top:1px;font-style:normal}
.badge.red{background:var(--red)}
.badge.green{background:#6bbf3e;line-height:13px;padding:0}
.viewall{left:267px;top:795px;font-size:6.8px;font-weight:500;color:var(--dark)}
.search-by{left:434px;top:457px;width:169px;height:117px;padding:10px 11px}
.stabs{display:flex;gap:1px;font-size:6.2px;color:var(--dark)}
.stabs span{padding:5px 7px;background:#fff;border:1px solid var(--line);border-bottom:none}
.stabs span+span{background:#e6e6e6}
.slist{background:#fff;border:1px solid var(--line)}
.slist div{height:19px;border-bottom:1px solid var(--line);padding:5px 7px;font-size:6.5px;display:flex;justify-content:space-between}
.slist div:last-child{border-bottom:none}
.vac{left:434px;top:582px;width:169px;height:239px;background:#fff}
.vac h3{height:20px;background:var(--sky);color:#1d3f5a;font-size:8.5px;font-weight:500;padding:5px 9px}
.vac ul{list-style:none;padding:5px 10px}
.vac li{height:14px;font-size:6.3px;display:flex;align-items:center;gap:6px}
.vac li svg{width:6px;height:6px}
.vac .more{position:absolute;right:10px;bottom:4px;color:var(--red);font-size:6.3px;font-weight:500}
.sect{font-size:10px;font-weight:500}
.course{position:absolute;top:851px;width:169px;height:154px;border:1px solid var(--line);border-radius:2px;background:#fff}
.course .img{position:absolute;left:14px;top:7px;width:141px;height:83px}
.course .cap{position:absolute;left:14px;top:78px;width:141px;height:13px;background:rgba(0,0,0,.65);color:#fff;font-size:6.8px;padding:2px 6px}
.course p{position:absolute;left:20px;top:95px;width:130px;font-size:4.8px;line-height:5.5px;color:#222}
.course p b{color:var(--orange-text);font-weight:400}
.course .try{position:absolute;left:20px;top:126px;width:74px;height:13px;background:var(--orange);color:#fff;font-size:5px;text-align:center;padding-top:4px;font-weight:500}
.course .brand{position:absolute;right:20px;top:127px;font-size:8px;color:#333;display:flex;gap:3px;align-items:center}
.course .brand i{width:10px;height:10px;background:var(--orange);display:block}
.sponsor{left:434px;top:856px;width:169px;height:149px;background:linear-gradient(150deg,#333 0 44%,#7ccad8 44%)}
.sponsor .nr{position:absolute;right:8px;top:8px;font-size:5.5px;color:#fff;display:flex;gap:3px;align-items:center}
.sponsor .nr i{width:10px;height:10px;border-radius:50%;background:#fff;display:block}
.sponsor .art{position:absolute;left:42px;top:38px;width:72px;height:34px;background:#d8c06a;border-radius:6px}
.sponsor .t1{position:absolute;left:0;width:169px;top:78px;text-align:center;font-size:13px;color:#222}
.sponsor .t2{position:absolute;left:0;width:169px;top:97px;text-align:center;font-size:9.5px;color:#234}
.sponsor .cta{position:absolute;left:36px;top:113px;width:96px;height:20px;background:#e54434;color:#fff;border-radius:2px;font-size:9px;text-align:center;padding-top:5px}
.hostbar{left:133px;top:1014px;width:410px;height:51px;background:linear-gradient(#2b2f36,#121417);color:#ddd;font-size:17px;font-weight:700;text-align:center;padding-top:15px;letter-spacing:.5px}
.footer{left:0;top:1074px;width:676px;height:126px;background:var(--sky)}
.flogo{left:74px;top:30px;color:#fff;font-size:13px;display:flex;align-items:center;gap:5px}
.flogo i{width:14px;height:14px;border-radius:50%;background:#fff;display:block}
.copy{left:74px;top:68px;font-size:6.2px;line-height:10.5px;color:#2f5060}
.fvac{left:258px;top:9px;width:230px;height:19px;background:var(--sky-deep);color:#fff;text-align:center;font-size:9px;font-weight:500;padding-top:4px;border-radius:2px}
.fcol{top:35px;text-align:center;font-size:6.3px;line-height:10.8px;color:#2a4a5a}
.fcol h4{color:var(--orange-text);font-size:7.3px;font-weight:500;line-height:11px}
.chat{left:530px;top:1139px;width:122px;height:37px;background:#f6a94a;border-radius:10px;border:2px solid #fff;padding:4px 9px}
.chat b{font-size:9px;color:#3a2a10;display:block}
.chat span{font-size:5px;color:#fff;display:block;text-align:right}
.chat .x{position:absolute;right:8px;top:2px;font-size:6px;color:#333}
.offline{left:532px;top:1186px;width:132px;height:14px;background:#2a2a2a;color:#fff;font-size:6px;padding:3px 6px;display:flex;align-items:center;gap:4px}
.offline i{width:7px;height:7px;border-radius:50%;background:#888;display:block}
.x10{left:663px;top:1177px;font-size:6px;font-weight:700;color:#222}
</style>
</head>
<body>

<div class="abs topbar">Advertising Job VACANCY &nbsp;|&nbsp; LOGIN / REGISTER</div>

<div class="abs logo"><span class="mark"></span>Lumari Novo</div>

<div class="abs promo">
  <div class="left">Espaço para Empresas e Profissionais de<br>Beleza, Estética e Bem-estar</div>
  <div class="right">Anuncie GRÁTIS sua<br>VAGA de EMPREGO!</div>
</div>

<nav class="abs nav"><span>Home</span><span>Blog</span><span>For Professional</span><span>For Business</span><span>Events &amp; Partners</span><span>About Us</span><span>Contact Us</span></nav>

<div class="abs hero" role="img" aria-label="Photo of a hairdresser cutting a smiling client's blonde fringe in a salon"></div>

<div class="abs search">
  <h2>Local Job Search and desired!</h2>
  <div class="row"><div class="field">Keyword Search..</div><div class="btn">SEARCH</div></div>
  <div class="ex"><b>Ex:</b> Manicure São Paulo, Rio de Janeiro Hairdresser</div>
</div>
<div class="abs dots"><i></i><i></i><i></i><i></i></div>

<section class="abs subscribe">
  <div class="abs title">Subscribe by Email</div>
  <div class="abs desc">Enter your email address to subscribe and receive notifications of new posts by email.</div>
  <div class="abs email">Enter Email</div>
  <div class="abs sbtn">SUBSCRIBE</div>
  <div class="abs follow">Follow Us On</div>
  <div class="abs social">
    <i style="background:#3b5a9a"></i><i style="background:#55b6e4"></i><i style="background:#c9c9c9"></i><i style="background:#e8662a"></i>
  </div>
</section>

<div class="abs panel" style="left:73px;top:457px;width:349px;height:365px"></div>
<div class="abs tabs"><div class="tab on">Featured Job Vacancies</div><div class="tab">Latest Job Vacancies</div></div>
<div class="abs jobs">
  <div class="job" style="top:10px">
    <div class="head"><span class="c1">Company</span><span class="c2">Job Name</span><span class="c3">Location</span><span class="c4">Date</span></div>
    <div class="body">
      <div class="c1"><div class="thumb" role="img" aria-label="Company thumbnail"></div></div>
      <div class="c2"><span class="g">Aux. Hairdresser (Escovista)<br>Santo André (SP)</span><br>Marina Costa / Ônix Hair and Esthetics</div>
      <div class="c3"><span class="g">Santo André</span><br><span class="small">São Paulo, the Federative Republic of Brazil</span></div>
      <div class="c4 g">July 18, 2013</div>
    </div>
    <div class="foot"><span>Posted by: <em>Marina Costa</em></span><span class="badge red">Registered<br>(CLT)</span></div>
  </div>
  <div class="job" style="top:107px">
    <div class="head"><span class="c1">Company</span><span class="c2">Job Name</span><span class="c3">Location</span><span class="c4">Date</span></div>
    <div class="body">
      <div class="c1"><div class="thumb" role="img" aria-label="Company thumbnail" style="background:linear-gradient(135deg,#f7c23a,#d8402a)"></div></div>
      <div class="c2"><span class="g">Aux. Hairdresser (Escovista)<br>Santo André (SP)</span><br>Marina Costa / Ônix Hair and Esthetics</div>
      <div class="c3"><span class="g">Santo André</span><br><span class="small">São Paulo, the Federative Republic of Brazil</span></div>
      <div class="c4 g">July 18, 2013</div>
    </div>
    <div class="foot"><span>Posted by: <em>Marina Costa</em></span><span class="badge green">Autonomous</span></div>
  </div>
  <div class="job" style="top:204px">
    <div class="head"><span class="c1">Company</span><span class="c2">Job Name</span><span class="c3">Location</span><span class="c4">Date</span></div>
    <div class="body">
      <div class="c1"><div class="thumb" role="img" aria-label="Company thumbnail" style="background:linear-gradient(135deg,#f4e2d0,#d9b28c)"></div></div>
      <div class="c2"><span class="g">Aux. Hairdresser (Escovista)<br>Santo André (SP)</span><br>Marina Costa / Ônix Hair and Esthetics</div>
      <div class="c3"><span class="g">Santo André</span><br><span class="small">São Paulo, the Federative Republic of Brazil</span></div>
      <div class="c4 g">July 18, 2013</div>
    </div>
    <div class="foot"><span>Posted by: <em>Marina Costa</em></span><span class="badge red">Registered<br>(CLT)</span></div>
  </div>
</div>
<div class="abs viewall">View All Jobs &gt;&gt;</div>

<aside class="abs panel search-by">
  <div class="stabs"><span>Search by</span><span>Tags</span></div>
  <div class="slist">
    <div>Job Type Job<span>›</span></div><div>Salary job<span>›</span></div><div>Job Category<span>›</span></div><div>Published Date<span>›</span></div>
  </div>
</aside>

<aside class="abs panel vac">
  <h3>Job Vacancies</h3>
  <ul>
    <li><svg viewBox="0 0 6 6"><path d="M.5 3l1.8 1.8L5.5 1" stroke="#6bbf3e" fill="none" stroke-width="1"/></svg>Assistant Hairdresser</li>
    <li><svg viewBox="0 0 6 6"><path d="M.5 3l1.8 1.8L5.5 1" stroke="#6bbf3e" fill="none" stroke-width="1"/></svg>Assistant Cleaning</li>
    <li><svg viewBox="0 0 6 6"><path d="M.5 3l1.8 1.8L5.5 1" stroke="#6bbf3e" fill="none" stroke-width="1"/></svg>Hairdresser</li>
    <li><svg viewBox="0 0 6 6"><path d="M.5 3l1.8 1.8L5.5 1" stroke="#6bbf3e" fill="none" stroke-width="1"/></svg>Epilator</li>
    <li><svg viewBox="0 0 6 6"><path d="M.5 3l1.8 1.8L5.5 1" stroke="#6bbf3e" fill="none" stroke-width="1"/></svg>Designer Eyebrow</li>
    <li><svg viewBox="0 0 6 6"><path d="M.5 3l1.8 1.8L5.5 1" stroke="#6bbf3e" fill="none" stroke-width="1"/></svg>Featured</li>
    <li><svg viewBox="0 0 6 6"><path d="M.5 3l1.8 1.8L5.5 1" stroke="#6bbf3e" fill="none" stroke-width="1"/></svg>Nurse</li>
    <li><svg viewBox="0 0 6 6"><path d="M.5 3l1.8 1.8L5.5 1" stroke="#6bbf3e" fill="none" stroke-width="1"/></svg>Beautician</li>
    <li><svg viewBox="0 0 6 6"><path d="M.5 3l1.8 1.8L5.5 1" stroke="#6bbf3e" fill="none" stroke-width="1"/></svg>Physiotherapist</li>
    <li><svg viewBox="0 0 6 6"><path d="M.5 3l1.8 1.8L5.5 1" stroke="#6bbf3e" fill="none" stroke-width="1"/></svg>Management / Coordination</li>
    <li><svg viewBox="0 0 6 6"><path d="M.5 3l1.8 1.8L5.5 1" stroke="#6bbf3e" fill="none" stroke-width="1"/></svg>Manicure and Pedicure</li>
    <li><svg viewBox="0 0 6 6"><path d="M.5 3l1.8 1.8L5.5 1" stroke="#6bbf3e" fill="none" stroke-width="1"/></svg>Makeup artist</li>
    <li><svg viewBox="0 0 6 6"><path d="M.5 3l1.8 1.8L5.5 1" stroke="#6bbf3e" fill="none" stroke-width="1"/></svg>Massage therapist</li>
    <li><svg viewBox="0 0 6 6"><path d="M.5 3l1.8 1.8L5.5 1" stroke="#6bbf3e" fill="none" stroke-width="1"/></svg>Other</li>
  </ul>
  <div class="more">More Vacancies &gt;&gt;</div>
</aside>

<h2 class="abs sect" style="left:73px;top:832px;color:var(--orange-text)">Online Courses Aprendo</h2>
<h2 class="abs sect" style="left:434px;top:832px;color:var(--dark)">Sponsor</h2>

<div class="course" style="left:73px">
  <div class="img" role="img" aria-label="Makeup brush with pink powder" style="background:linear-gradient(135deg,#5a2a3c,#c56e86 60%,#e9c3c8)"></div>
  <div class="cap">Curso de Maquiagem Profissional</div>
  <p>Seja um profissional mais qualificado, invista na sua carreira e se prepare para o mercado de trabalho. Matricule-se agora no curso Aprendo de <b>Maquiagem Profissional</b>.</p>
  <div class="try">EXPERIMENTE GRÁTIS</div>
  <div class="brand">Aprendo<i></i></div>
</div>
<div class="course" style="left:253px">
  <div class="img" role="img" aria-label="Hairdresser cutting a client's hair" style="background:linear-gradient(135deg,#8a6e58,#d8c5b0 55%,#efe6dc)"></div>
  <div class="cap">Curso de Cabeleireiro Profissional</div>
  <p>Seja um profissional mais qualificado, invista na sua carreira e se prepare para o mercado de trabalho. Matricule-se agora no curso Aprendo de <b>Cabeleireiro Profissional</b>.</p>
  <div class="try">EXPERIMENTE GRÁTIS</div>
  <div class="brand">Aprendo<i></i></div>
</div>

<div class="abs sponsor">
  <div class="nr"><i></i>Nuvora</div>
  <div class="art" role="img" aria-label="Illustration of two fists"></div>
  <div class="t1">—YOU LIVIN' IT?—</div>
  <div class="t2">Deploy for this FREE Shirt</div>
  <div class="cta">Get Your Shirt</div>
</div>

<div class="abs hostbar">Orbitel Host</div>

<footer class="abs footer">
  <div class="abs flogo"><i></i>Lumari Novo</div>
  <div class="abs copy">Copyright 2013 @ Lumari Novo<br>Your Community for Professionals and<br>Companies Beauty, Aesthetics and Wellness</div>
  <div class="abs fvac">Job Vacancies</div>
  <div class="abs fcol" style="left:252px;width:70px"><h4>Beauty:</h4>Aux Hairdresser<br>Aux Escovista<br>Hairdresser<br>Epilator<br>Manicure<br>Makeup<br>Eyebrow Designer</div>
  <div class="abs fcol" style="left:316px;width:90px"><h4>Health and Wellness:</h4>Esthetician<br>Massage Therapist<br>Podiatrist<br>Physiotherapist<br>Nurse</div>
  <div class="abs fcol" style="left:411px;width:80px"><h4>Sales and Admin:</h4>Reception<br>Sale Cosmetics<br>Auxiliary Cleaning<br>Management</div>
</footer>

<div class="abs chat"><span class="x">×</span><b>Perguntas?</b><span>Clique para falar conosco!</span></div>
<div class="abs x10">x10</div>
<div class="abs offline"><i></i><b>Offline</b> - Deixe sua Mensagem!</div>

</body>
</html>
```